Social Media App Needs PPT Template

We need a PowerPoint template for a new social media company based in the DC area called "Bold Ledger." We provide an interactive digital platform for executives to share actionable advice. We would like to see designs that use our orange logo color as an accent, but are mainly grey, white, and black. The final design should communicate clean, chic, modern, and professional.

Target Market(s)

Executives

Industry/Entity Type

Information Technology

Font styles to use
Sans Serif

Colors
f78f20
fbe7d2
ffffff
000000
e8e8e8
757575

Requirements
Must have
• My project must have title page and many options for the body of the ppt (graphs, tables, etc). It also needs to be easy to modify. I must have someone who is experienced in creating powerpoint templates.
Nice to have
• It would be nice to have a very modern and clean design that includes the logo on every page, but still leaves a lot of room for the content of the slide
Should not have
• My design project should not look to busy.

```html
<!DOCTYPE html>
<html lang="en">
<head>
<meta charset="utf-8">
<title>Bold Ledger – Table Slide</title>
<link href="https://fonts.googleapis.com/css2?family=Lato:wght@300;400;700&display=swap" rel="stylesheet">
<style>
  :root {
    --stage: #cccccc;
    --paper: #ffffff;
    --sidebar: #222c3a;
    --accent: #f39321;
    --accent-soft: #f8c07e;
    --ink: #3a3a3a;
    --muted: #8a8a8a;
    --rule: #7a7a7a;
    --footer-rule: #4a5368;
    --side-text: #d8dbe0;
  }
  * { box-sizing: border-box; margin: 0; padding: 0; }
  html, body {
    width: 1200px; height: 960px; overflow: hidden;
    background: var(--stage);
    font-family: "Lato", sans-serif;
  }
  body { position: relative; }
  .page-label {
    position: absolute; top: 66px; left: 36px; width: 1164px;
    text-align: center; color: var(--paper);
    font-weight: 300; font-size: 32px; line-height: 1; letter-spacing: 1px;
  }
  .slide {
    position: absolute; left: 120px; top: 143px;
    width: 958px; height: 718px; background: var(--paper); overflow: hidden;
  }
  .sidebar {
    position: absolute; left: 0; top: 0; width: 170px; height: 100%;
    background: var(--sidebar);
  }
  .brand {
    position: absolute; left: 0; top: 90px; width: 170px;
    display: flex; flex-direction: column; align-items: center; gap: 12px;
    color: var(--accent); font-weight: 700; font-size: 22px; line-height: 1; text-align: center;
  }
  .brand-dot {
    width: 34px; height: 34px; border-radius: 50%; background: var(--accent);
  }
  .site {
    position: absolute; left: 20px; top: 676px;
    color: var(--side-text); font-size: 18px; font-weight: 400; line-height: 1;
  }
  .title {
    position: absolute; left: 205px; top: 102px;
    color: var(--accent); font-size: 42px; font-weight: 400; line-height: 1;
  }
  .title-rule {
    position: absolute; left: 205px; top: 155px; width: 716px; height: 1px;
    background: var(--accent-soft);
  }
  .table-rule {
    position: absolute; left: 200px; top: 236px; width: 725px; height: 1.5px;
    background: var(--rule);
  }
  .data-table {
    position: absolute; left: 198px; top: 262px; width: 727px;
    border-collapse: collapse; table-layout: fixed;
  }
  .data-table th {
    height: 48px; color: var(--muted); font-size: 15px; font-weight: 700;
    text-align: center; vertical-align: top; line-height: 1;
  }
  .data-table td {
    height: 72.5px; text-align: center; font-size: 27px; font-weight: 400;
    color: var(--ink); line-height: 1;
  }
  .col-label { width: 280px; }
  .col-num { width: 140px; }
  .col-end { width: 27px; }
  .data-table td.row-label {
    text-align: left; padding-left: 90px; font-size: 18px; font-weight: 400;
  }
  .data-table tr.highlight td { background: var(--accent); color: var(--paper); }
  .footer-rule {
    position: absolute; left: 802px; top: 664px; width: 124px; height: 1px;
    background: var(--footer-rule);
  }
  .page-number {
    position: absolute; right: 36px; top: 683px;
    color: var(--muted); font-size: 13px; line-height: 1;
  }
</style>
</head>
<body>
  <div class="page-label">Page 7</div>
  <section class="slide">
    <aside class="sidebar">
      <div class="brand">
        <span class="brand-dot"></span>
        <span>Bold Ledger</span>
      </div>
      <div class="site">boldledger.com</div>
    </aside>
    <h1 class="title">Title of the page</h1>
    <div class="title-rule"></div>
    <div class="table-rule"></div>
    <table class="data-table">
      <colgroup>
        <col class="col-label"><col class="col-num"><col class="col-num"><col class="col-num"><col class="col-end">
      </colgroup>
      <thead>
        <tr><th></th><th>A</th><th>B</th><th>C</th><th></th></tr>
      </thead>
      <tbody>
        <tr class="highlight"><td class="row-label">Type 1</td><td>20</td><td>30</td><td>40</td><td></td></tr>
        <tr><td class="row-label">Type 2</td><td>50</td><td>60</td><td>70</td><td></td></tr>
        <tr class="highlight"><td class="row-label">Type 3</td><td>80</td><td>90</td><td>100</td><td></td></tr>
      </tbody>
    </table>
    <div class="footer-rule"></div>
    <div class="page-number">Page 6</div>
  </section>
</body>
</html>
```